Tuition Center Website

We need a new web site for a tutoring company based in sydney.

We only teach senior highschool students and pride ourselves on building the students abilities to think their way through life.

I would like a bright and vibrant website that looks professional and modern.
It needs to look simple and neat but also have the functionality we need.
Images and flash would be good.

Please keep in mind that the site must be appealing to a younger audience.

We need a multipage website with the following navigation bars:

1.Home (As logo not "home" button)
I would like a news box/ticker somewhere that can stream our chatterbook and pipstream feeds and also any news updates we want to put up.
Subscribe to newsletter button.

2. About us.
This needs to be a pull down into:
-What we do
-Why we do it
-How we do it

3. Courses
Pulldown into:
-Maths
-English
-Science
(we may need to attach extra pages behind these e.g. Courses/Science/Physics or Courses/Science/Chemistry and possibly add a link to a new zandlo form)

4. Inspired
This page is like a blog page where we can upload videos, links to articles that we find to be inspiring and hopefully will inspire others.

5. Inspire
This is a recruitment page. Only content here.

6. Contact us.
Mapquill map widget and a 'contact us' form

* Our branding requires green close to #12FF3D

***Please have a look at the current website.
@ www.velmorlearning.com.au

Thanks everybody hope the revision of my brief is better and more informative than my last one

Target Market(s)

senior highschool students aged 15-19, parents ( to a lesser degree)

Industry/Entity Type

It Company

Requirements
Must have
• Ability to change content on pages.

The green doesn't have to be everywhere, but it must be obvious that it is our colour.

Nice to have
• Sites with a nicer mix of images and flash will be given more consideration. But then again, if you amaze us, you amaze us and we will go with your design.
Should not have
• Should stay away from ocre, brown colours and serif fonts.

```html
<!DOCTYPE html>
<html lang="en">
<head>
<meta charset="utf-8">
<title>About Us – Velmor Learning</title>
<link href="https://fonts.googleapis.com/css2?family=Open+Sans:wght@300;400;600;700&display=swap" rel="stylesheet">
<style>
:root{
  --green:#8ae000;
  --green-light:#a3ef1c;
  --green-dark:#72c400;
  --heading-green:#6cb70a;
  --ink:#111;
  --text:#3a3a3a;
  --nav-text:#4a5a20;
  --grey-bg:#f4f4f4;
  --box-bg:#ebeaea;
  --box-line:#d0d0d0;
  --footer:#2b2b2b;
  --white:#fff;
}
*{box-sizing:border-box;margin:0;padding:0}
html,body{width:1080px;height:1200px;overflow:hidden}
body{font-family:"Open Sans",Arial,sans-serif;background:var(--white);color:var(--text);position:relative}
.wrap{width:864px;margin:0 auto;position:relative}

.site-header{height:120px;border-bottom:1px solid #ddd}
.site-header .wrap{height:120px;display:flex;justify-content:space-between;align-items:center}
.brand{display:flex;align-items:center;gap:10px}
.brand-square{width:30px;height:30px;background:var(--green)}
.brand-name{font-size:22px;font-weight:700;color:var(--green-dark)}
.callout{text-align:right}
.callout-top{display:flex;align-items:center;justify-content:flex-end;gap:6px;color:#4a4f78;font-size:15px;font-weight:300;line-height:17px;text-align:left}
.callout-phone{font-size:27px;color:#222;font-weight:400;margin-top:2px;letter-spacing:.3px}

.main-nav{height:48px;background:linear-gradient(var(--green-light),var(--green));border-bottom:1px solid var(--green-dark)}
.main-nav .wrap{height:48px}
.nav-list{list-style:none}
.nav-list li{position:absolute;top:13px;font-size:13px;line-height:16px;font-weight:700;color:var(--nav-text);padding:3px 7px;white-space:nowrap;text-shadow:0 1px 0 rgba(255,255,255,.5)}
.nav-list li.is-active{background:var(--white);color:#333;border-radius:3px;box-shadow:0 0 0 1px #cfe9a0}
.nav-home{left:13px}
.nav-about{left:97px}
.nav-courses{left:206px}
.nav-inspired{left:309px}
.nav-inspire{left:412px}
.nav-contact{left:509px}
.follow{position:absolute;right:0;top:16px;display:flex;align-items:center;gap:9px;font-size:12px;line-height:16px;font-weight:700;color:#5d7a1a;white-space:nowrap}
.follow .net{color:var(--white);font-size:12px}

.hero{height:309px;position:relative;background:linear-gradient(90deg,#7a8272 0%,#a7ab9a 30%,#e5e1da 45%,#d9cfc5 65%,#c9bdb6 100%)}
.hero-title{position:absolute;left:108px;top:124px;font-size:44px;line-height:60px;font-weight:300;color:var(--white);text-shadow:0 1px 3px rgba(0,0,0,.5);letter-spacing:-.5px}

.intro-band{height:90px;background:var(--green);border-top:2px solid #d8f2a8;display:flex;align-items:center}
.intro-band p{font-size:20px;font-weight:700;color:#111;line-height:29px;text-shadow:0 1px 1px rgba(255,255,255,.6);letter-spacing:-.2px}

.what{height:246px;padding-top:34px;border-bottom:1px solid #e2e2e2}
.section-title{display:flex;align-items:center;gap:6px;font-size:22px;font-weight:700;color:var(--ink)}
.section-title::after{content:"";flex:1;height:5px;background:#f1f1f1}
.what p{font-size:13px;line-height:19px;margin-top:18px;color:#444}
.what p + p{margin-top:18px}

.details{height:332px;background:var(--grey-bg)}
.details .wrap{display:flex;justify-content:space-between;padding-top:16px}
.detail{width:421px}
.detail h3{font-size:22px;font-weight:600;color:var(--heading-green);margin-left:1px}
.detail-box{margin-top:16px;height:253px;border:1px solid var(--box-line);border-radius:4px;background:var(--box-bg);box-shadow:inset 0 0 0 3px #f7f7f7;padding:16px 14px}
.detail-box p{font-size:12px;line-height:18px;color:#222}
.detail-box ul{list-style:none;margin-top:12px}
.detail-box li{font-size:13.5px;line-height:27px;color:#222;padding-left:30px;position:relative}
.detail-box li::before{content:"";position:absolute;left:9px;top:10px;width:8px;height:8px;border-radius:50%;background:#333}
.details .detail:last-child{width:422px}

.site-footer{position:absolute;left:0;right:0;bottom:0;height:55px;background:linear-gradient(var(--footer),#3a3a3a);border-top:3px solid #1a1a1a}
.site-footer .wrap{height:52px;display:flex;align-items:center;justify-content:space-between;color:#eee;font-size:12px}
.footer-nav{display:flex;gap:13px;list-style:none;font-size:12.5px;white-space:nowrap}
</style>
</head>
<body>

<header class="site-header">
  <div class="wrap">
    <div class="brand">
      <span class="brand-square"></span>
      <span class="brand-name">Velmor Learning</span>
    </div>
    <div class="callout">
      <div class="callout-top">
        <svg width="32" height="32" viewBox="0 0 32 32" aria-hidden="true">
          <path d="M6 18 V14 a10 10 0 0 1 20 0 V18" fill="none" stroke="#333" stroke-width="2.5"/>
          <rect x="3" y="15" width="6" height="9" rx="2" fill="#333"/>
          <rect x="23" y="15" width="6" height="9" rx="2" fill="#333"/>
          <path d="M26 24 q0 5 -8 5" fill="none" stroke="#333" stroke-width="1.5"/>
          <circle cx="17" cy="29" r="1.8" fill="#333"/>
        </svg>
        <span>Call for a<br>free Consultation !</span>
      </div>
      <div class="callout-phone">303-555-0147</div>
    </div>
  </div>
</header>

<nav class="main-nav">
  <div class="wrap">
    <ul class="nav-list">
      <li class="nav-home">Home</li>
      <li class="nav-about is-active">About Us</li>
      <li class="nav-courses">Courses</li>
      <li class="nav-inspired">Inspired</li>
      <li class="nav-inspire">Inspire</li>
      <li class="nav-contact">Contact Us</li>
    </ul>
    <div class="follow">Follow Us <span class="net">Netlinq</span><span class="net">chatterbook</span><span class="net">pipstream</span></div>
  </div>
</nav>

<section class="hero" role="img" aria-label="Photo of a smiling group of young tutors standing together in a bright office">
  <h1 class="hero-title">ABOUT US</h1>
</section>

<section class="intro-band">
  <div class="wrap">
    <p>Velmor Learning are HSC mentors and tutors who aim to build real relationships and offer you the help you need. HSC tutoring is different at Velmor – in a good way.</p>
  </div>
</section>

<section class="what">
  <div class="wrap">
    <h2 class="section-title">What we do</h2>
    <p>Le Lorem Ipsum est simplement du faux texte employé dans la composition et la mise en page avant impression. Le Lorem Ipsum est le faux texte standard de l'imprimerie depuis les années 1500, quand un peintre anonyme assembla ensemble des morceaux de texte pour réaliser un livre spécimen de polices de texte.</p>
    <p>Il n'a pas fait que survivre cinq siècles, mais s'est aussi adapté à la bureautique informatique, sans que son contenu n'en soit modifié. Il a été popularisé dans les années 1960 grâce à la vente de feuilles Tramsheet contenant des passages du Lorem Ipsum, et, plus récemment, par son inclusion dans des applications de mise en page de texte, comme Orvel PageSetter.</p>
  </div>
</section>

<section class="details">
  <div class="wrap">
    <article class="detail">
      <h3>Why we do it</h3>
      <div class="detail-box">
        <p>On sait depuis longtemps que travailler avec du texte lisible etcont enant du sens est source de distractions, et empêche de secon centrer sur la mise en page elle-même. L'avantage du Lorem Ipsum sur un texte générique comme.</p>
        <ul>
          <li>Plusieurs variations de Lorem Ipsum</li>
          <li>Peuvent être trouvées ici ou là</li>
          <li>Mais la majeure partie d'entre elles a été altérée par</li>
          <li>Addition d'humour ou de mots aléatoires qui ne</li>
          <li>Ressemblent pas une seconde à du texte standard.</li>
        </ul>
      </div>
    </article>
    <article class="detail">
      <h3>How we do it</h3>
      <div class="detail-box">
        <p>On sait depuis longtemps que travailler avec du texte lisible etcont enant du sens est source de distractions, et empêche de secon centrer sur la mise en page elle-même. L'avantage du Lorem Ipsum sur un texte générique comme.</p>
        <ul>
          <li>Plusieurs variations de Lorem Ipsum</li>
          <li>Peuvent être trouvées ici ou là</li>
          <li>Mais la majeure partie d'entre elles a été altérée par</li>
          <li>Addition d'humour ou de mots aléatoires qui ne</li>
          <li>Ressemblent pas une seconde à du texte standard.</li>
        </ul>
      </div>
    </article>
  </div>
</section>

<footer class="site-footer">
  <div class="wrap">
    <span>© Velmor Learning. All rights reserved.</span>
    <ul class="footer-nav">
      <li>Home</li>
      <li>About Us</li>
      <li>Courses</li>
      <li>Inspired</li>
      <li>Inspire</li>
      <li>Contact Us</li>
    </ul>
  </div>
</footer>

</body>
</html>
```